BUSINESS CARD - HALLORAN FIELD SERVICES

I would like to create a business card for my fertilizer spreading business. I would like to incorporate my existing logo and also a description of the services offered. The business card will be given to farmers so must be kept simple but effective. It will also be left in stores so much also be eye catching in order to stand out from other cards.

Target Market(s)

FARMERS

Requirements
Must have
• FRONT OF CARD = EXISTING LOGO + "CUSTOMISED SPREADING" below the logo

REAR Of CARD = SERVICES OFFERED AND CONTACT DETAILS

- Bulk fertilizer including Lime, Gypsum, Manure & Compost
- Granular fertilizer including Single Super, Urea, Gran-am, & Custom Blends
- Modern equipment - Autosteer & Variable Rate Capable
- Friendly & Reliable Service
- Contact Gus: 0417 552 308
Nice to have
• utilize same color scheme as existing logo

```html
<!DOCTYPE html>
<html lang="en">
<head>
<meta charset="utf-8">
<title>Halloran Field Services – Business Card</title>
<link href="https://fonts.googleapis.com/css2?family=Arimo:wght@400;700&display=swap" rel="stylesheet">
<style>
  :root {
    --stage: #2b2b2b;
    --card-light: #ffffff;
    --card-dark: #4c4c4d;
    --ink-dark: #4a4a4b;
    --ink-light: #ffffff;
    --accent: #f7941d;
    --faint-light: #e6e6e6;
    --faint-dark: #555556;
  }
  * { box-sizing: border-box; margin: 0; padding: 0; }
  html, body { width: 1200px; height: 866px; overflow: hidden; }
  body {
    background: var(--stage);
    font-family: "Arimo", Arial, sans-serif;
    display: flex;
    align-items: center;
    justify-content: center;
    gap: 40px;
  }
  .card {
    position: relative;
    width: 560px;
    height: 320px;
    overflow: hidden;
    box-shadow: 0 10px 24px rgba(0,0,0,0.45);
  }
  .card--front { background: var(--card-light); }
  .card--back { background: var(--card-dark); color: var(--ink-light); }

  .backdrop-art {
    position: absolute;
    right: -20px;
    bottom: -30px;
    width: 360px;
    height: 280px;
    border-radius: 45% 55% 20% 30%;
  }
  .card--front .backdrop-art {
    background: radial-gradient(ellipse at 50% 45%, var(--faint-light) 0%, var(--faint-light) 55%, rgba(230,230,230,0) 75%);
  }
  .card--back .backdrop-art {
    background: radial-gradient(ellipse at 50% 45%, var(--faint-dark) 0%, var(--faint-dark) 55%, rgba(85,85,86,0) 75%);
  }

  .front-brand {
    position: absolute;
    inset: 0;
    display: flex;
    flex-direction: column;
    align-items: center;
    justify-content: center;
    gap: 14px;
  }
  .brand-dot {
    width: 92px;
    height: 92px;
    border-radius: 50%;
    background: var(--ink-dark);
  }
  .brand-name {
    font-weight: 700;
    font-size: 30px;
    letter-spacing: 0.5px;
    color: var(--ink-dark);
  }
  .tagline {
    font-size: 16px;
    letter-spacing: 2px;
    color: var(--accent);
  }

  .back-content {
    position: absolute;
    left: 34px;
    top: 30px;
    right: 30px;
  }
  .card--back .brand-name {
    color: var(--ink-light);
    font-size: 26px;
  }
  .rule {
    height: 2px;
    width: 380px;
    background: var(--accent);
    margin: 8px 0 14px;
  }
  .services { list-style: none; font-size: 13px; line-height: 1.35; }
  .services li { position: relative; padding-left: 16px; }
  .services li::before {
    content: "";
    position: absolute;
    left: 0;
    top: 5px;
    width: 8px;
    height: 8px;
    border-radius: 50%;
    background: var(--accent);
  }
  .contact {
    position: absolute;
    right: 32px;
    bottom: 26px;
    text-align: right;
  }
  .contact-label { font-size: 16px; color: var(--ink-light); }
  .contact-phone { font-size: 20px; color: var(--accent); margin-top: 4px; }
</style>
</head>
<body>
  <section class="card card--front">
    <div class="backdrop-art" role="img" aria-label="Faint silhouette of cattle in a paddock"></div>
    <div class="front-brand">
      <div class="brand-dot"></div>
      <div class="brand-name">HALLORAN FIELD SERVICES</div>
      <div class="tagline">CUSTOMISED SPREADING</div>
    </div>
  </section>

  <section class="card card--back">
    <div class="backdrop-art" role="img" aria-label="Faint silhouette of cattle in a paddock"></div>
    <div class="back-content">
      <div class="brand-name">HALLORAN FIELD SERVICES</div>
      <div class="rule"></div>
      <ul class="services">
        <li>Bulk fertilizer including Lime<br>Gypsum, Manure &amp; Compost</li>
        <li>Granular fertilizer including Single<br>Super, Urea, Gran-am, &amp; Custom Blends</li>
        <li>Modern equipment</li>
        <li>Autosteer &amp; Variable Rate Capable</li>
        <li>Friendly &amp; Reliable Service</li>
      </ul>
    </div>
    <div class="contact">
      <div class="contact-label">Contact</div>
      <div class="contact-phone">Gus: 0417 552 308</div>
    </div>
  </section>
</body>
</html>
```